Redo our website for our Robotics company

We sell robotic equipment to the restaurant industry. Our current robot, is a cooking robot that cooks up to 15 lbs of food. We will provide a prior website as well as brand guidelines. We plan on using wordpress and take advantage of wordpress's visual (no code) editor.

Current website - https://kelvatrix88.com/ (please note we are only selling Tammo now and no longer selling Plavo+

We want someone to take our existing content and design the website as well as layout our content we provide. Here's a suggested site layout:

✅ KelvaTrix88 Website Wireframe / Site Map
1. Home

Purpose: Introduce Tammo, establish credibility, drive demo requests.

Sections:

Hero Section

Headline: “Meet Tammo — Your New Robotic Chef for High-Volume, Consistent Cooking.”

Sub-headline: Increase throughput. Reduce labor. Deliver perfect food every time.

CTA: Request a Demo + Watch Tammo Cook

Visual: Video loop or hero animation of Tammo in action.

How Tammo Works (3-4 steps)

Step cards: Load Ingredients → Select Recipe → Tammo Cooks → Serve

Icons and short explanations.

Key Benefits

Labor savings

Zero inconsistency

24/7 uptime

Throughput increases (30–50% faster)

Health & safety compliance

Who It’s For

QSR restaurants

Fast casual

Catering/commissaries

Ghost kitchens

Case Studies / Testimonials

Logo bar + quotes

“Tammo helped us reduce cooking times by 40%.”

Video Section

“Watch Tammo cook a full batch from start to finish.”

CTA Section

Big banner: Book a Demo

2. Product: “Meet Tammo”

Purpose: Deep dive into hardware, software, safety, reliability.

Sections:

Overview

What Tammo is

What tasks it automates

Where it fits in a kitchen

Hardware Features

High-temperature cooking chamber

Precision sensors

Automated stirring

Automated dispensing

Safety mechanisms (locking lids, auto-shutoff)

Software & AI

Recipe automation

IoT dashboard

Remote monitoring

Predictive maintenance

Specs Table

Dimensions

Power requirements

Capacity (lbs per batch)

Safety certifications

Gallery

Close-ups, installation photos, process shots

CTA: Request a Demo

3. Solutions

Purpose: Show that Tammo solves real operational problems.

Sub-pages or sections:

For Quick-Service Restaurants

Reduce labor cost

Speed up peak-hour demand

For Catering & Commissaries

Large-batch consistency

Automate repetitive cooking tasks

For High-Growth Chains

Replicable quality across multiple locations

Centralized recipe control

Each solution page includes:

A problem statement

How Tammo solves it

Metrics / KPIs

Relevant testimonial

CTA

4. ROI / Economics

Purpose: Sell the financial story clearly.

Sections:

Savings Calculator

Labor hours saved

Cost savings

Throughput increases

Food waste reduction

Before & After Comparison

Traditional kitchen vs. robotic kitchen

Sample ROI

“Payback in as little as 3–6 months.”

Download Full ROI Report (PDF)

5. Case Studies

Purpose: Social proof + real results.

Structure for each case study:

Customer background

Problem

Implementation

KPIs achieved

Labor savings

Consistency improvements

Cooking speed

Quote + photos/video

6. Pricing

Purpose: Start a commercial conversation.

Include:

Subscription model (monthly / annual)

Hardware leasing or purchase options

Installation + training

Support level

CTA to book a sales call

7. About

Purpose: Build trust.

Sections:

Mission statement

Founding team

Advisors/partners

“Why we built Tammo”

8. Resources

Purpose: SEO + education.

Subpages:

Blog (e.g., “The Future of Automated Kitchens”)

Whitepapers

Technical documentation

Product videos

9. Contact

General inquiry form

Sales contact

Support portal

Careers

```html
<!DOCTYPE html>
<html lang="en">
<head>
<meta charset="utf-8">
<title>KelvaTrix88 — Meet Tammo</title>
<link rel="stylesheet" href="https://fonts.googleapis.com/css2?family=Montserrat:wght@700;800&family=Oswald:wght@300;400;500&family=Roboto+Condensed:wght@500;700&display=swap">
<style>
:root{
  --red:#ef2f2c;
  --orange:#ff7a3a;
  --grad:linear-gradient(90deg,#ee2c2c,#ff8a42);
  --ink:#1b1b1b;
  --text:#333;
  --muted:#666;
  --peach:#fbe6de;
  --hero-bg:#ececec;
  --white:#fff;
}
*{margin:0;padding:0;box-sizing:border-box}
html,body{width:1200px;height:4926px;overflow:hidden;background:var(--white)}
.page{position:relative;width:1200px;height:4926px;overflow:hidden;font-family:"Oswald",sans-serif;color:var(--text)}
.abs{position:absolute}
.brand{font-family:"Montserrat",sans-serif;font-weight:800;color:var(--red);letter-spacing:-1px;white-space:nowrap}
.sec-title{position:absolute;left:0;width:1200px;text-align:center;font-family:"Montserrat",sans-serif;font-weight:800;font-size:44px;color:var(--ink)}
.hl{display:inline-block;background:var(--grad);color:var(--white);padding:0 18px;transform:skewX(-14deg);margin-left:4px}
.hl span{display:inline-block;transform:skewX(14deg)}

/* hero */
.hero-bg{left:0;top:0;width:1200px;height:840px;background:radial-gradient(ellipse at 70% 80%,#f7f7f7 0%,var(--hero-bg) 60%,#e6e6e6 100%)}
.hero-fade{left:0;top:700px;width:1200px;height:160px;background:linear-gradient(#ececec00,#fff)}
.logo-top{left:0;top:30px;width:1200px;text-align:center;font-size:46px}
.nav{left:143px;top:118px;width:918px;height:50px;background:var(--grad);clip-path:polygon(3% 0,100% 0,97% 100%,0 100%);display:flex;align-items:center;padding-left:120px;gap:0}
.nav a{font-family:"Roboto Condensed",sans-serif;font-weight:700;font-size:15px;color:var(--white);text-decoration:none;text-transform:uppercase;padding:0 16px}
.nav-home{left:140px;top:114px;width:96px;height:56px;background:var(--white);border:3px solid var(--red);transform:skewX(-16deg);display:flex;align-items:center;justify-content:center}
.nav-home span{transform:skewX(16deg);font-family:"Roboto Condensed",sans-serif;font-weight:700;font-size:15px;color:var(--red)}
.hero-title{left:143px;top:258px;font-family:"Montserrat",sans-serif;font-weight:800;font-size:45px;line-height:54px;color:var(--ink)}
.hero-title .accent{color:var(--red)}
.hero-sub{left:140px;top:500px;font-family:"Oswald",sans-serif;font-weight:300;font-size:25px;line-height:40px;color:var(--ink)}
.btn-demo{left:148px;top:615px;width:222px;height:54px;background:var(--grad);transform:skewX(-16deg);display:flex;align-items:center;justify-content:center}
.btn-demo span{transform:skewX(16deg);font-family:"Roboto Condensed",sans-serif;font-weight:700;font-size:16px;color:var(--white)}
.watch-link{left:394px;top:632px;font-family:"Roboto Condensed",sans-serif;font-weight:700;font-size:15px;color:var(--red);text-decoration:underline;display:flex;align-items:center;gap:8px}
.hero-frame{left:700px;top:269px;width:472px;height:392px;border:3px solid var(--orange);border-radius:26px;transform:skewX(-8deg)}
.hero-media{left:726px;top:269px;width:448px;height:392px;border-radius:26px;background:linear-gradient(160deg,#3a3d42 0%,#8a8d92 45%,#cfd1d3 70%,#6e7074 100%);transform:skewX(-8deg);overflow:hidden}
.play{position:absolute;border-radius:50%;background:var(--red);display:flex;align-items:center;justify-content:center;box-shadow:0 0 0 8px #ffffff55}

/* steps */
.step{position:absolute;width:240px;text-align:center}
.step-box{position:relative;margin:0 auto;width:126px;height:106px;border:3px solid var(--orange);transform:skewX(-10deg);background:var(--white)}
.step-icon{position:absolute;left:50%;top:50%;transform:translate(-50%,-50%) skewX(10deg)}
.step-num{position:absolute;left:-26px;top:-22px;width:40px;height:40px;border-radius:50%;background:var(--orange);color:var(--white);font-family:"Montserrat",sans-serif;font-weight:700;font-size:14px;display:flex;align-items:center;justify-content:center;transform:skewX(10deg)}
.step h3{margin-top:22px;font-family:"Roboto Condensed",sans-serif;font-weight:700;font-size:19px;line-height:26px;color:var(--ink)}
.step p{margin-top:10px;font-weight:300;font-size:16px;line-height:26px;color:var(--muted)}
.step .chev{margin-top:16px}

/* benefits */
.benefit-panel{left:38px;top:1420px;width:1124px;height:693px;background:var(--peach);clip-path:polygon(11% 0,100% 0,100% 3%,91% 100%,0 100%,0 96%);border-radius:40px}
.ring{left:426px;top:1611px;width:324px;height:324px;border-radius:50%;border:3px solid var(--orange)}
.ring-inner{left:480px;top:1665px;width:216px;height:216px;border-radius:50%;background:var(--white);box-shadow:0 0 0 14px #fde0d4,0 0 40px #f9b49a}
.center-logo{left:480px;top:1755px;width:216px;text-align:center;font-size:30px}
.b-icon{position:absolute;width:66px;height:66px;border-radius:50%;background:var(--red);display:flex;align-items:center;justify-content:center;box-shadow:0 0 0 6px #fff}
.b-label{position:absolute;font-weight:400;font-size:21px;line-height:30px;color:var(--ink)}

/* who it's for */
.who-img{position:absolute;width:216px;height:245px;clip-path:polygon(8% 0,100% 0,92% 100%,0 100%)}
.who-label{position:absolute;width:216px;text-align:center;font-family:"Roboto Condensed",sans-serif;font-weight:700;font-size:20px;color:var(--ink)}

/* testimonials */
.testi-frame{left:71px;top:2796px;width:984px;height:392px;border:3px solid var(--orange);border-radius:30px;transform:skewX(-6deg)}
.testi-body{left:92px;top:2796px;width:963px;height:392px;border-radius:30px;background:var(--grad);transform:skewX(-6deg);overflow:hidden}
.testi-photo{left:0;top:0;width:480px;height:392px;background:linear-gradient(135deg,#2a1a10,#7a4a22 45%,#c08040 70%,#3a2414)}
.testi-title{left:608px;top:2862px;font-family:"Montserrat",sans-serif;font-weight:800;font-size:45px;color:var(--white)}
.testi-quote{left:608px;top:2940px;width:380px;font-weight:300;font-style:italic;font-size:19px;line-height:27px;color:var(--white)}
.testi-author{left:608px;top:3094px;font-weight:500;font-style:italic;font-size:20px;color:var(--white);display:flex;align-items:center;gap:24px}
.stars{letter-spacing:3px;font-size:22px;font-style:normal}
.arrow-btn{position:absolute;width:36px;height:36px;border-radius:50%;border:2px solid currentColor;display:flex;align-items:center;justify-content:center}

/* clients */
.client{position:absolute;top:3421px;width:288px;height:120px;background:var(--white);border:2px solid #ddd;border-radius:14px;transform:skewX(-12deg);box-shadow:0 6px 16px #0000000f;display:flex;align-items:center;justify-content:center}
.client.active{border-color:var(--orange);box-shadow:0 10px 24px #ff7a3a33}
.client span{transform:skewX(12deg);font-family:"Montserrat",sans-serif;font-weight:800;font-size:24px;color:var(--ink);display:flex;align-items:center;gap:10px}
.client i{display:inline-block;width:22px;height:22px;background:var(--ink)}
.client-quote{left:0;top:3586px;width:1200px;text-align:center;font-weight:300;font-style:italic;font-size:24px;color:var(--ink)}

/* video */
.video-frame{left:96px;top:3690px;width:1000px;height:480px;border:2px solid #f4a58a;border-radius:30px;transform:rotate(2deg) skewX(-6deg)}
.video{left:128px;top:3721px;width:945px;height:449px;border-radius:34px;background:#050505;transform:skewX(-5deg);overflow:hidden}
.video-media{left:140px;top:0;width:720px;height:449px;background:linear-gradient(180deg,#1c2330,#3c3f44 40%,#6a5a44 70%,#1a1a1a)}
.video-cap{left:140px;top:340px;width:720px;height:64px;background:#00000099;display:flex;align-items:center;justify-content:center;font-family:"Montserrat",sans-serif;font-weight:800;font-size:24px;color:var(--white)}
.video-cap em{font-style:normal;color:var(--orange);margin-left:8px}

/* cta */
.cta{left:13px;top:4275px;width:1176px;height:201px;background:var(--grad);clip-path:polygon(0 0,100% 0,97% 100%,4% 100%);border-radius:24px}
.cta h2{position:absolute;left:127px;top:66px;font-family:"Montserrat",sans-serif;font-weight:800;font-size:48px;color:var(--white)}
.cta-btn{position:absolute;left:818px;top:74px;width:222px;height:50px;border:2px solid var(--white);transform:skewX(-16deg);display:flex;align-items:center;justify-content:center}
.cta-btn span{transform:skewX(16deg);font-family:"Roboto Condensed",sans-serif;font-weight:700;font-size:16px;color:var(--white)}

/* footer */
.footer-bg{left:0;top:4476px;width:1200px;height:450px;background:linear-gradient(#fff,#efefef)}
.logo-foot{left:0;top:4535px;width:1200px;text-align:center;font-size:46px}
.foot-nav{left:0;top:4638px;width:1200px;display:flex;justify-content:center;gap:34px}
.foot-nav a{font-family:"Roboto Condensed",sans-serif;font-weight:700;font-size:16px;color:var(--ink);text-decoration:none;text-transform:uppercase}
.foot-contact{left:0;top:4698px;width:1200px;display:flex;justify-content:center;align-items:center;gap:16px;font-size:19px;color:var(--ink)}
.foot-contact .item{display:flex;align-items:center;gap:10px}
.foot-legal{left:0;top:4758px;width:1200px;text-align:center;font-weight:300;font-size:16px;color:var(--ink)}
.social{left:0;top:4826px;width:1200px;display:flex;justify-content:center;gap:22px}
.social .s{display:flex;align-items:center;gap:6px;font-family:"Roboto Condensed",sans-serif;font-weight:500;font-size:13px;color:var(--ink)}
.social .dot{width:34px;height:34px;border-radius:50%;background:var(--red)}
.social .dot.alt{background:var(--white);border:2px solid var(--ink)}
.foot-line{left:0;top:4918px;width:1200px;height:8px;background:var(--grad)}
</style>
</head>
<body>
<div class="page">

  <!-- Hero -->
  <div class="abs hero-bg"></div>
  <div class="abs hero-fade"></div>
  <div class="abs brand logo-top">KelvaTrix88</div>

  <nav class="abs nav">
    <a>Product</a><a>Solutions</a><a>ROI</a><a>Case Studies</a><a>Pricing</a><a>About</a><a>Resources</a><a>Contact</a>
  </nav>
  <div class="abs nav-home"><span>HOME</span></div>

  <h1 class="abs hero-title">Meet Tammo<br><span class="accent">Your New Robotic</span><br>Chef for High-Volume,<br><span class="accent">Consistent Cooking.</span></h1>
  <p class="abs hero-sub">Increase throughput. Reduce labor.<br>Deliver perfect food every time.</p>
  <div class="abs btn-demo"><span>REQUEST A DEMO</span></div>
  <div class="abs watch-link"><svg width="12" height="14" viewBox="0 0 12 14"><path d="M0 0L12 7L0 14Z" fill="#ef2f2c"/></svg>WATCH TAMMO COOK</div>

  <div class="abs hero-frame"></div>
  <div class="abs hero-media" role="img" aria-label="Tammo cooking robots lined up in a commercial kitchen">
    <div class="play" style="left:200px;top:150px;width:86px;height:86px"><svg width="28" height="32" viewBox="0 0 28 32"><path d="M2 0L28 16L2 32Z" fill="#fff"/></svg></div>
  </div>

  <!-- How it works -->
  <h2 class="sec-title" style="top:888px">How Tammo <span class="hl"><span>Works</span></span></h2>

  <svg class="abs" style="left:300px;top:1060px" width="600" height="60" viewBox="0 0 600 60" fill="none" stroke="#888" stroke-width="2" stroke-dasharray="6 6">
    <path d="M0 30 C40 55 90 55 118 36"/>
    <path d="M248 36 C290 5 340 5 368 30"/>
    <path d="M494 36 C530 55 570 55 598 30"/>
  </svg>

  <div class="step" style="left:109px;top:1041px">
    <div class="step-box"><div class="step-num">01</div>
      <svg class="step-icon" width="56" height="56" viewBox="0 0 56 56" fill="none" stroke="#ef2f2c" stroke-width="2.5"><circle cx="28" cy="28" r="25"/><circle cx="28" cy="28" r="17"/><path d="M28 40V18M28 26c-5-1-7-5-7-8 4 0 7 3 7 8zM28 26c5-1 7-5 7-8-4 0-7 3-7 8zM28 33c-5-1-7-5-7-8 4 0 7 3 7 8zM28 33c5-1 7-5 7-8-4 0-7 3-7 8z"/></svg>
    </div>
    <h3>Load<br>Ingredients</h3>
    <p>Sed ut perspiciatis unde omnis<br>iste natus error sit</p>
    <svg class="chev" width="30" height="30" viewBox="0 0 30 30" fill="none" stroke="#ef2f2c" stroke-width="2"><circle cx="15" cy="15" r="13"/><path d="M9 12l6 6 6-6"/></svg>
  </div>

  <div class="step" style="left:356px;top:1041px">
    <div class="step-box"><div class="step-num">02</div>
      <svg class="step-icon" width="48" height="56" viewBox="0 0 48 56" fill="none" stroke="#ef2f2c" stroke-width="2.5"><rect x="6" y="4" width="36" height="48" rx="3"/><path d="M12 4v48"/><circle cx="27" cy="22" r="7"/><path d="M19 38h16M19 44h16"/></svg>
    </div>
    <h3>Select Recipe</h3>
    <p>Sed ut perspiciatis unde omnis<br>iste natus error sit voluptatem<br>accusantium doloremque</p>
    <svg class="chev" width="30" height="30" viewBox="0 0 30 30" fill="none" stroke="#ef2f2c" stroke-width="2"><circle cx="15" cy="15" r="13"/><path d="M9 12l6 6 6-6"/></svg>
  </div>

  <div class="step" style="left:602px;top:1041px">
    <div class="step-box"><div class="step-num">03</div>
      <svg class="step-icon" width="60" height="56" viewBox="0 0 60 56" fill="none" stroke="#ef2f2c" stroke-width="2.5"><path d="M22 4c-4 5 4 8 0 13M30 2c-4 5 4 8 0 13M38 4c-4 5 4 8 0 13"/><path d="M4 26h52M10 26v18a8 8 0 0 0 8 8h24a8 8 0 0 0 8-8V26"/><rect x="24" y="20" width="12" height="6"/></svg>
    </div>
    <h3>Tammo Cooks</h3>
    <p>Sed ut perspiciatis unde omnis<br>iste natus error sit voluptatem<br>accusantium doloremque</p>
    <svg class="chev" width="30" height="30" viewBox="0 0 30 30" fill="none" stroke="#ef2f2c" stroke-width="2"><circle cx="15" cy="15" r="13"/><path d="M9 12l6 6 6-6"/></svg>
  </div>

  <div class="step" style="left:849px;top:1041px">
    <div class="step-box"><div class="step-num">04</div>
      <svg class="step-icon" width="60" height="56" viewBox="0 0 60 56" fill="none" stroke="#ef2f2c" stroke-width="2.5"><circle cx="30" cy="10" r="4"/><path d="M8 36a22 22 0 0 1 44 0zM4 36h52M14 44h28l6-4"/></svg>
    </div>
    <h3>Serve</h3>
    <p>Sed ut perspiciatis unde omnis<br>iste natus error sit voluptatem<br>accusantium doloremque</p>
    <svg class="chev" width="30" height="30" viewBox="0 0 30 30" fill="none" stroke="#ef2f2c" stroke-width="2"><circle cx="15" cy="15" r="13"/><path d="M9 12l6 6 6-6"/></svg>
  </div>

  <!-- Key benefits -->
  <div class="abs benefit-panel"></div>
  <h2 class="sec-title" style="top:1484px">Key <span class="hl"><span>Benefits</span></span></h2>
  <div class="abs ring"></div>
  <div class="abs ring-inner"></div>
  <div class="abs brand center-logo">KelvaTrix88</div>

  <div class="b-icon" style="left:414px;top:1645px"><svg width="28" height="28" viewBox="0 0 28 28" fill="none" stroke="#fff" stroke-width="3"><path d="M22 10A9 9 0 0 0 6 10M6 18a9 9 0 0 0 16 0"/><path d="M22 4v6h-6M6 24v-6h6"/></svg></div>
  <div class="b-label" style="left:240px;top:1662px">Zero inconsistency</div>

  <div class="b-icon" style="left:695px;top:1645px"><svg width="28" height="28" viewBox="0 0 28 28"><circle cx="14" cy="14" r="12" fill="#fff"/><path d="M14 7v8l5 3" stroke="#ef2f2c" stroke-width="3" fill="none"/></svg></div>
  <div class="b-label" style="left:780px;top:1662px">24/7 uptime</div>

  <div class="b-icon" style="left:391px;top:1817px"><svg width="28" height="28" viewBox="0 0 28 28"><path d="M3 5h11l11 11-9 9L5 14z" fill="#fff"/><circle cx="9" cy="10" r="2.5" fill="#ef2f2c"/></svg></div>
  <div class="b-label" style="left:251px;top:1834px">Labor savings</div>

  <div class="b-icon" style="left:695px;top:1817px"><svg width="24" height="28" viewBox="0 0 24 28"><path d="M14 1L2 16h9l-2 11 12-15h-9z" fill="#fff"/></svg></div>
  <div class="b-label" style="left:780px;top:1818px">Throughput increases<br>(30–50% faster)</div>

  <div class="b-icon" style="left:555px;top:1916px;box-shadow:0 0 0 6px #fff,0 0 0 9px #f9a07f"><svg width="26" height="24" viewBox="0 0 26 24"><path d="M13 22S2 15 2 8a5.5 5.5 0 0 1 11-2 5.5 5.5 0 0 1 11 2c0 7-11 14-11 14z" fill="#fff"/></svg></div>
  <div class="b-label" style="left:490px;top:1992px;width:200px;text-align:center">Health &amp; safety<br>compliance</div>

  <!-- Who it's for -->
  <h2 class="sec-title" style="top:2216px">Who <span class="hl"><span>It’s For</span></span></h2>
  <div class="who-img" style="left:148px;top:2329px;background:linear-gradient(160deg,#5a2a12,#c0702a 45%,#6a1a10 80%,#2a0e08)" role="img" aria-label="Quick-service restaurant dining room"></div>
  <div class="who-label" style="left:146px;top:2596px">QSR Restaurants</div>
  <div class="who-img" style="left:376px;top:2402px;background:linear-gradient(150deg,#d8d8d8,#4a4a4a 40%,#2a2a2a 70%,#9a9a9a)" role="img" aria-label="Cooking drum with a fast-casual dish">
    <div style="position:absolute;left:84px;top:100px;width:44px;height:44px;border-radius:50%;background:var(--orange);color:#fff;font-size:26px;line-height:44px;text-align:center;font-family:'Montserrat',sans-serif">+</div>
  </div>
  <div class="who-label" style="left:380px;top:2668px">Fast casual</div>
  <div class="who-img" style="left:600px;top:2329px;background:linear-gradient(160deg,#b8c0c4,#eef0f0 40%,#8a9498 75%,#c8ccce)" role="img" aria-label="Catering staff working in a commissary kitchen"></div>
  <div class="who-label" style="left:602px;top:2596px">Catering</div>
  <div class="who-img" style="left:824px;top:2402px;background:linear-gradient(160deg,#3a3c3e,#5a5c5e 45%,#8a6a48 80%,#2e2e2e)" role="img" aria-label="Compact ghost kitchen workspace"></div>
  <div class="who-label" style="left:830px;top:2668px">Ghost kitchens</div>

  <!-- Testimonials -->
  <div class="abs testi-frame"></div>
  <div class="abs testi-body">
    <div class="abs testi-photo" role="img" aria-label="Friends sharing a meal at a busy restaurant"></div>
  </div>
  <h2 class="abs testi-title">Testimonials</h2>
  <p class="abs testi-quote">“Sed ut perspiciatis unde omnis iste natus error sit voluptatem accusantium d laudantium, totam rem aperiam, eaque ipsa quae ab illo inventore veritatis et quasi architecto beatae vitae dicta sunt exen quia voluptas sit aspernatur”</p>
  <div class="abs testi-author">-Dana Reyes <span class="stars">★★★★★</span></div>
  <div class="arrow-btn" style="left:922px;top:3118px;color:#fff"><svg width="12" height="14" viewBox="0 0 12 14" fill="none" stroke="#fff" stroke-width="2"><path d="M9 1L3 7l6 6"/></svg></div>
  <div class="arrow-btn" style="left:962px;top:3118px;color:#fff"><svg width="12" height="14" viewBox="0 0 12 14" fill="none" stroke="#fff" stroke-width="2"><path d="M3 1l6 6-6 6"/></svg></div>

  <!-- Clients -->
  <h2 class="sec-title" style="top:3302px">Our <span class="hl"><span>Clients</span></span></h2>
  <div class="arrow-btn" style="left:91px;top:3464px;color:#666"><svg width="12" height="14" viewBox="0 0 12 14" fill="none" stroke="#666" stroke-width="2"><path d="M9 1L3 7l6 6"/></svg></div>
  <div class="client" style="left:154px"><span><i></i>Norvale</span></div>
  <div class="client active" style="left:456px"><span>Brightpan</span></div>
  <div class="client" style="left:758px"><span>Foundry Co</span></div>
  <div class="arrow-btn" style="left:1071px;top:3464px;color:#666"><svg width="12" height="14" viewBox="0 0 12 14" fill="none" stroke="#666" stroke-width="2"><path d="M3 1l6 6-6 6"/></svg></div>
  <p class="abs client-quote">“Tammo helped us reduce cooking times by 40%.”</p>

  <!-- Video -->
  <div class="abs video-frame"></div>
  <div class="abs video">
    <div class="abs video-media" role="img" aria-label="Tammo stirring a full batch inside its cooking drum"></div>
    <div class="play" style="left:428px;top:135px;width:90px;height:90px"><svg width="28" height="32" viewBox="0 0 28 32"><path d="M2 0L28 16L2 32Z" fill="#fff"/></svg></div>
    <div class="abs video-cap">Watch Tammo cook a full batch <em>from start to finish.</em></div>
  </div>

  <!-- CTA -->
  <section class="abs cta">
    <h2>Enhance, Not Replace.</h2>
    <div class="cta-btn"><span>BOOK A DEMO</span></div>
  </section>

  <!-- Footer -->
  <div class="abs footer-bg"></div>
  <div class="abs brand logo-foot">KelvaTrix88</div>
  <nav class="abs foot-nav">
    <a>Home</a><a>Product</a><a>Solutions</a><a>ROI</a><a>Case Studies</a><a>Pricing</a><a>About</a><a>Resources</a><a>Contact</a>
  </nav>
  <div class="abs foot-contact">
    <span class="item"><svg width="20" height="16" viewBox="0 0 20 16"><rect width="20" height="16" rx="2" fill="#ef2f2c"/><path d="M1 2l9 7 9-7" stroke="#fff" stroke-width="2" fill="none"/></svg>info@kelvatrix88.com</span>
    <span>|</span>
    <span class="item"><svg width="18" height="18" viewBox="0 0 24 24"><path d="M6.6 10.8a15 15 0 0 0 6.6 6.6l2.2-2.2a1 1 0 0 1 1-.25 11.4 11.4 0 0 0 3.6.57 1 1 0 0 1 1 1V20a1 1 0 0 1-1 1A17 17 0 0 1 3 4a1 1 0 0 1 1-1h3.5a1 1 0 0 1 1 1c0 1.25.2 2.45.57 3.57a1 1 0 0 1-.25 1z" fill="#ef2f2c"/></svg>+1 [877] 555 0142</span>
  </div>
  <p class="abs foot-legal">KelvaTrix88 © 2025. All Rights Reserved.&nbsp; | &nbsp;Privacy Policy&nbsp; | &nbsp;Terms of Use</p>
  <div class="abs social">
    <span class="s"><span class="dot"></span>Snapwell</span>
    <span class="s"><span class="dot alt"></span>Postline</span>
    <span class="s"><span class="dot"></span>Friendly</span>
  </div>
  <div class="abs foot-line"></div>
</div>
</body>
</html>
```